Agriculture farming Hemp and CBD

The logo is in works with your company now, should be ready in a few days. We have our Domain (kestrelbrookhollow.com) We would like to see incorporated seed to growth, but not necessary. we would like to nature colors and some black and green. we have our farm and will be growing and selling HEMP and CBD we are based in the state of Virginia. Would like to incorporate the words pause, play, rewind if possible but not necessary.

Target Market(s)

20 years old to elderly

Coding

Coded - Design and coding required

Number of Pages Required

3 page

Font styles to use
Serif

Requirements
Must have
• I'm not sure on the must haves, we are open to any ideas, we would definitely like to see Hemp and CBD included, may the life cycle of seed to plant. We must have a pop up asking if you are 20 years old before they can enter our site and to view or purchase our product. I want the design to be totally different than what i uploaded.
Nice to have
• Would like to see natural colors as well as black and green
Should not have
• I want

```html
<!DOCTYPE html>
<html lang="en">
<head>
<meta charset="utf-8">
<title>Kestrel Brook Hollow – Home and Age Check</title>
<link href="https://fonts.googleapis.com/css2?family=Roboto+Slab:wght@400;500;700&family=Lato:wght@400;700&display=swap" rel="stylesheet">
<style>
:root{
  --green:#56b834;
  --green-dark:#3f8f22;
  --black:#000;
  --ink:#222;
  --muted:#8a8a8a;
  --canvas:#ebebeb;
  --white:#fff;
  --red:#e8141b;
  --star:#f3a21b;
  --line:#e3e3e3;
}
*{box-sizing:border-box;margin:0;padding:0}
html,body{width:720px;height:1200px;overflow:hidden;background:var(--canvas)}
body{font-family:'Lato',sans-serif;color:var(--ink)}
.board{position:absolute;left:0;top:0;width:1484px;height:2474px;transform:scale(0.48518);transform-origin:0 0}
.page{position:absolute;top:88px;width:693px;height:2298px;background:var(--white);overflow:hidden}
.page--home{left:28px}
.page--gate{left:763px}
.abs{position:absolute}
.serif{font-family:'Roboto Slab',serif}

/* header */
.site-header{left:0;top:0;width:693px;height:50px;background:var(--black)}
.brand{left:65px;top:16px;color:var(--white);font:700 13px 'Lato',sans-serif;letter-spacing:.2px}
.nav{right:64px;top:19px;display:flex;gap:14px;font-size:9px;color:var(--white);text-transform:uppercase}
.nav .active{color:var(--green)}
.nav svg{width:9px;height:9px}

/* hero */
.hero-photo{left:0;top:50px;width:693px;height:360px;background:linear-gradient(180deg,#9aa3a6 0%,#6f8a6a 22%,#3f6e2c 45%,#2f5c1f 70%,#4c7a2c 100%)}
.hero-wave{left:0;top:290px;width:693px;height:130px}
.hero-title{left:306px;top:166px;font:500 23px 'Roboto Slab',serif;color:var(--white);text-transform:uppercase}
.hero-text{left:306px;top:198px;width:330px;font-size:8.5px;line-height:18px;color:var(--white)}
.btn{display:flex;align-items:center;justify-content:center;border-radius:15px;background:var(--green);color:#101;font:400 9px 'Roboto Slab',serif;text-transform:uppercase}
.hero-btn{left:306px;top:242px;width:90px;height:27px}
.chev{color:var(--white);font-size:16px}

/* about */
.about-title{left:67px;top:484px;font:500 24px 'Roboto Slab',serif;text-transform:uppercase}
.body-copy{font-size:9px;line-height:20px;color:var(--muted);text-align:justify}
.about-text{left:65px;top:520px;width:285px}
.about-btn{left:65px;top:655px;width:89px;height:30px}
.about-photo{left:380px;top:463px;width:248px;height:248px;border-radius:50%;border:3px solid var(--white);box-shadow:0 0 0 1px #ddd;background:radial-gradient(circle at 55% 65%,#c9b43a 0%,#8aa52c 28%,#3f7f2a 60%,#2d5f22 100%)}

/* products */
.products{left:0;top:768px;width:693px;height:347px;background:linear-gradient(180deg,#2b2d2b 0%,#24331f 45%,#27401c 100%)}
.section-title{font:500 23px 'Roboto Slab',serif;text-transform:uppercase;text-align:center;width:693px;left:0}
.products-title{top:792px;color:var(--white)}
.product-card{top:830px;width:183px;height:256px;background:var(--white);border-bottom:2px solid var(--green)}
.product-photo{width:183px;height:148px}
.product-card h3{margin:12px 8px 6px;font:700 8px 'Roboto Slab',serif;text-transform:uppercase;color:var(--ink)}
.product-card p{margin:0 8px;font-size:7.6px;line-height:15px;color:var(--muted);text-align:justify}

/* video */
.video-photo{left:60px;top:1174px;width:273px;height:252px;background:linear-gradient(135deg,#c5c93a 0%,#7fa62a 40%,#3f7526 75%,#2c5a1f 100%)}
.play{left:172px;top:1278px;width:45px;height:45px;border-radius:50%;background:var(--green);display:flex;align-items:center;justify-content:center}
.video-title{left:354px;top:1199px;font:500 24px 'Roboto Slab',serif;text-transform:uppercase}
.video-text{left:354px;top:1236px;width:285px}
.video-btn{left:354px;top:1370px;width:89px;height:29px}

/* reviews */
.reviews-title{top:1482px;color:var(--ink)}
.review-card{top:1522px;width:185px;height:167px;border:2px solid var(--line);padding:10px 8px}
.quote{font:700 40px/30px 'Roboto Slab',serif;color:var(--green);height:26px}
.review-card p{font-size:7.4px;line-height:14.5px;color:var(--muted);font-style:italic;text-align:justify;margin-top:6px}
.reviewer{font-size:8px;color:var(--ink);margin-top:10px;text-transform:uppercase}
.stars{color:var(--star);font-size:8px;letter-spacing:1px;margin-top:3px}
.chev-dark{color:#333;font-size:16px}

/* team band */
.team-band{left:0;top:1749px;width:693px;height:191px;background:linear-gradient(180deg,#5cbf3a,#4fb02f)}
.team-text{left:70px;top:1780px;width:553px;font-size:8.5px;line-height:19.5px;color:var(--white);text-align:center}
.team-btn{left:292px;top:1872px;width:108px;height:29px;background:var(--white)}

/* newsletter */
.news-title{top:1993px;color:var(--ink)}
.news-sub{top:2028px;width:693px;left:0;text-align:center;font-size:8.5px;color:var(--muted)}
.field{top:2056px;width:139px;height:30px;border:1px solid var(--line);font-size:8.5px;color:var(--muted);padding:10px 5px}
.signup{left:491px;top:2056px;width:138px;height:30px;background:var(--green);color:var(--white);font-size:8.5px;display:flex;align-items:center;justify-content:center;text-transform:uppercase}

/* footer */
.site-footer{left:0;top:2147px;width:693px;height:151px;background:var(--black)}
.footer-brand{top:2172px;width:693px;left:0;text-align:center;color:var(--white);font:700 16px 'Lato',sans-serif}
.footer-links{top:2208px;left:0;width:693px;display:flex;justify-content:center;gap:22px;font-size:8.5px;color:var(--white)}
.socials{top:2235px;left:0;width:693px;display:flex;justify-content:center;gap:7px}
.socials span{width:21px;height:21px;border:1.5px solid var(--white);border-radius:50%}
.copyright{top:2270px;left:0;width:693px;text-align:center;font-size:8.5px;color:var(--white)}

/* age gate */
.dim{left:0;top:0;width:693px;height:2298px;background:rgba(0,0,0,.72)}
.gate{left:67px;top:169px;width:558px;height:296px;display:flex}
.gate-offer{width:258px;height:296px;background:linear-gradient(160deg,#7a7a5a 0%,#4c4a33 45%,#2d2b1f 100%);position:relative;color:var(--white);text-align:center}
.gate-offer h2{position:absolute;top:112px;width:258px;font:500 34px 'Roboto Slab',serif}
.gate-offer p{position:absolute;top:160px;left:24px;width:210px;font-size:9px;line-height:19px}
.gate-panel{width:300px;height:296px;background:var(--white);text-align:center;position:relative}
.gate-panel h2{margin-top:64px;font:500 23px 'Roboto Slab',serif;text-transform:uppercase}
.gate-panel h3{margin-top:12px;font:400 11px 'Roboto Slab',serif}
.gate-panel p{margin:8px auto 0;width:270px;font-size:8.5px;line-height:19.5px;color:var(--muted)}
.gate-actions{display:flex;justify-content:center;gap:14px;margin-top:12px}
.gate-actions span{width:89px;height:30px;display:flex;align-items:center;justify-content:center;color:var(--white);font-size:8.5px;text-transform:uppercase}
.agree{background:var(--green-dark)}
.decline{background:var(--red)}
.close{right:-16px;top:-14px;width:32px;height:32px;border-radius:50%;background:var(--red);color:var(--white);font:700 11px 'Lato',sans-serif;display:flex;align-items:center;justify-content:center;padding:6px 8px 0 0}
</style>
</head>
<body>
<div class="board">

<!-- Home page -->
<section class="page page--home">
  <header class="abs site-header">
    <div class="abs brand">kestrelbrookhollow.com</div>
    <nav class="abs nav"><span class="active">Home</span><span>About</span><span>Products</span><span>Events</span><span>Reviews</span><span>Contact</span><svg viewBox="0 0 10 10"><circle cx="4" cy="4" r="3" fill="none" stroke="#fff" stroke-width="1.3"/><path d="M6.3 6.3 9 9" stroke="#fff" stroke-width="1.3"/></svg></nav>
  </header>
  <div class="abs hero-photo" role="img" aria-label="Hemp plants growing in a field below misty mountains"></div>
  <svg class="abs hero-wave" viewBox="0 0 693 130" preserveAspectRatio="none"><path d="M0 84 C120 30 260 60 420 100 C540 128 640 90 693 66 L693 130 L0 130Z" fill="#fff"/><path d="M0 84 C120 30 260 60 420 100 C540 128 640 90 693 66" fill="none" stroke="#56b834" stroke-width="5"/></svg>
  <span class="abs chev" style="left:44px;top:206px">‹</span><span class="abs chev" style="left:634px;top:206px">›</span>
  <h1 class="abs hero-title">Kestrel Brook Hollow</h1>
  <p class="abs hero-text">Nemo enim ipsam voluptatem quia voluptas sit aspernatur aut odit aut fugit, sed quia consequuntur magni dolores eos qui ratione voluptate</p>
  <div class="abs btn hero-btn">Get Started</div>

  <h2 class="abs about-title">About Us</h2>
  <p class="abs body-copy about-text">Nemo enim ipsam voluptatem quia voluptas sit aspernatur aut odit aut fugit, sed quia consequuntur magni dolores eos qui ratione voluptatem sequi nesciunt. Neque porro quisquam est, qui dolorem ipsum quia dolor sit amet, consectetur, adipisci velit, sed quia non numquam eius modi tempora incidunt ut labore et dolore magnam aliquam quaerat voluptatem.</p>
  <div class="abs btn about-btn">Read More</div>
  <div class="abs about-photo" role="img" aria-label="Bottles of CBD oil on a table against green leaves"></div>

  <div class="abs products" role="img" aria-label="Dark hemp field backdrop"></div>
  <h2 class="abs section-title products-title">Our Products</h2>
  <span class="abs chev" style="left:48px;top:944px">‹</span><span class="abs chev" style="left:634px;top:944px">›</span>
  <article class="abs product-card" style="left:65px"><div class="product-photo" role="img" aria-label="Row of CBD oil vials" style="background:linear-gradient(180deg,#1f5a1c,#3d7c24 55%,#d8d3c0)"></div><h3>Lorem ipsum dolor sit</h3><p>Nemo enim ipsam voluptas sit aspernatur aut odit aut fugit, sed quia consequuntur magni dolores eos qui ratione voluptatem sequi nesciunt</p></article>
  <article class="abs product-card" style="left:256px"><div class="product-photo" role="img" aria-label="Dropper over a small oil bottle with hemp seeds" style="background:linear-gradient(180deg,#f2f1ec,#cfd8c2 45%,#6f8f3e 75%,#7a5a38)"></div><h3>Lorem ipsum dolor sit</h3><p>Nemo enim ipsam voluptas sit aspernatur aut odit aut fugit, sed quia consequuntur magni dolores eos qui ratione voluptatem sequi nesciunt</p></article>
  <article class="abs product-card" style="left:446px"><div class="product-photo" role="img" aria-label="Amber bottles, cream jar and a hemp leaf" style="background:linear-gradient(180deg,#4a3a2c,#6b4a2c 50%,#8c6a44)"></div><h3>Lorem ipsum dolor sit</h3><p>Nemo enim ipsam voluptas sit aspernatur aut odit aut fugit, sed quia consequuntur magni dolores eos qui ratione voluptatem sequi nesciunt</p></article>

  <div class="abs video-photo" role="img" aria-label="Gloved hands holding a beaker beside a hemp plant"></div>
  <div class="abs play"><svg width="14" height="16" viewBox="0 0 14 16"><path d="M2 1 13 8 2 15Z" fill="#fff"/></svg></div>
  <h2 class="abs video-title">Our Video</h2>
  <p class="abs body-copy video-text">Nemo enim ipsam voluptatem quia voluptas sit aspernatur aut odit aut fugit, sed quia consequuntur magni dolores eos qui ratione voluptatem sequi nesciunt. Neque porro quisquam est, qui dolorem ipsum quia dolor sit amet, consectetur, adipisci velit, sed quia non numquam eius modi tempora incidunt ut labore et dolore magnam aliquam quaerat voluptatem.</p>
  <div class="abs btn video-btn">Watch Video</div>

  <h2 class="abs section-title reviews-title">Customer Reviews</h2>
  <span class="abs chev-dark" style="left:50px;top:1596px">‹</span><span class="abs chev-dark" style="left:634px;top:1596px">›</span>
  <article class="abs review-card" style="left:63px"><div class="quote">“</div><p>Nemo enim ipsam voluptatem quia voluptas sit aspernatur aut odit aut fugit, sed quia consequuntur magni dolores eos qui ratione voluptatem sequi nesciunt. Neque porro quisquam</p><div class="reviewer">Mara Fenwick - USA</div><div class="stars">★★★★★</div></article>
  <article class="abs review-card" style="left:254px"><div class="quote">“</div><p>Nemo enim ipsam voluptatem quia voluptas sit aspernatur aut odit aut fugit, sed quia consequuntur magni dolores eos qui ratione voluptatem sequi nesciunt. Neque porro quisquam</p><div class="reviewer">Pete Calder - UK</div><div class="stars">★★★★★</div></article>
  <article class="abs review-card" style="left:444px"><div class="quote">“</div><p>Nemo enim ipsam voluptatem quia voluptas sit aspernatur aut odit aut fugit, sed quia consequuntur magni dolores eos qui ratione voluptatem sequi nesciunt. Neque porro quisquam</p><div class="reviewer">Anna Holloway - USA</div><div class="stars">★★★★★</div></article>

  <div class="abs team-band"></div>
  <p class="abs team-text">Nemo enim ipsam voluptatem quia voluptas sit aspernatur aut odit aut fugit, sed quia consequuntur magni dolores eos qui ratione voluptatem sequi nesciunt. Neque porro quisquam est, qui dolorem ipsum quia dolor sit amet, consectetur, adipisci velit, sed quia non numquam eius modi tempora incidunt ut labore et dolore magnam aliquam quaerat voluptatem. Ut enim ad minima veniam, quis nostrum exercitationem ullam corporis suscipit laboriosam, nisi ut aliquid ex ea commodi consequatur</p>
  <div class="abs btn team-btn">Meet the Team</div>

  <h2 class="abs section-title news-title">Newsletter Sign-Up</h2>
  <p class="abs news-sub">Sign up with your email address to receive news and updates.</p>
  <div class="abs field" style="left:65px">First Name</div>
  <div class="abs field" style="left:207px">Last Name</div>
  <div class="abs field" style="left:349px">Email Address</div>
  <div class="abs signup">Sign Up</div>

  <footer class="abs site-footer"></footer>
  <div class="abs footer-brand">kestrelbrookhollow.com</div>
  <div class="abs footer-links"><span>Shop</span><span>Terms &amp; Conditions</span><span>Privacy Policy</span><span>FAQs</span><span>Partnership enquiries</span></div>
  <div class="abs socials"><span></span><span></span><span></span><span></span></div>
  <div class="abs copyright">© 2020 All Rights Reserved</div>
</section>

<!-- Home page with age gate -->
<section class="page page--gate">
  <header class="abs site-header">
    <div class="abs brand">kestrelbrookhollow.com</div>
    <nav class="abs nav"><span class="active">Home</span><span>About</span><span>Products</span><span>Events</span><span>Reviews</span><span>Contact</span><svg viewBox="0 0 10 10"><circle cx="4" cy="4" r="3" fill="none" stroke="#fff" stroke-width="1.3"/><path d="M6.3 6.3 9 9" stroke="#fff" stroke-width="1.3"/></svg></nav>
  </header>
  <div class="abs hero-photo" role="img" aria-label="Hemp plants growing in a field below misty mountains"></div>
  <svg class="abs hero-wave" viewBox="0 0 693 130" preserveAspectRatio="none"><path d="M0 84 C120 30 260 60 420 100 C540 128 640 90 693 66 L693 130 L0 130Z" fill="#fff"/><path d="M0 84 C120 30 260 60 420 100 C540 128 640 90 693 66" fill="none" stroke="#56b834" stroke-width="5"/></svg>
  <h2 class="abs about-title">About Us</h2>
  <p class="abs body-copy about-text">Nemo enim ipsam voluptatem quia voluptas sit aspernatur aut odit aut fugit, sed quia consequuntur magni dolores eos qui ratione voluptatem sequi nesciunt. Neque porro quisquam est, qui dolorem ipsum quia dolor sit amet, consectetur, adipisci velit, sed quia non numquam eius modi tempora incidunt ut labore et dolore magnam aliquam quaerat voluptatem.</p>
  <div class="abs btn about-btn">Read More</div>
  <div class="abs about-photo" role="img" aria-label="Bottles of CBD oil on a table against green leaves"></div>

  <div class="abs products" role="img" aria-label="Dark hemp field backdrop"></div>
  <h2 class="abs section-title products-title">Our Products</h2>
  <article class="abs product-card" style="left:65px"><div class="product-photo" role="img" aria-label="Row of CBD oil vials" style="background:linear-gradient(180deg,#1f5a1c,#3d7c24 55%,#d8d3c0)"></div><h3>Lorem ipsum dolor sit</h3><p>Nemo enim ipsam voluptas sit aspernatur aut odit aut fugit, sed quia consequuntur magni dolores eos qui ratione voluptatem sequi nesciunt</p></article>
  <article class="abs product-card" style="left:256px"><div class="product-photo" role="img" aria-label="Dropper over a small oil bottle with hemp seeds" style="background:linear-gradient(180deg,#f2f1ec,#cfd8c2 45%,#6f8f3e 75%,#7a5a38)"></div><h3>Lorem ipsum dolor sit</h3><p>Nemo enim ipsam voluptas sit aspernatur aut odit aut fugit, sed quia consequuntur magni dolores eos qui ratione voluptatem sequi nesciunt</p></article>
  <article class="abs product-card" style="left:446px"><div class="product-photo" role="img" aria-label="Amber bottles, cream jar and a hemp leaf" style="background:linear-gradient(180deg,#4a3a2c,#6b4a2c 50%,#8c6a44)"></div><h3>Lorem ipsum dolor sit</h3><p>Nemo enim ipsam voluptas sit aspernatur aut odit aut fugit, sed quia consequuntur magni dolores eos qui ratione voluptatem sequi nesciunt</p></article>

  <div class="abs video-photo" role="img" aria-label="Gloved hands holding a beaker beside a hemp plant"></div>
  <div class="abs play"><svg width="14" height="16" viewBox="0 0 14 16"><path d="M2 1 13 8 2 15Z" fill="#fff"/></svg></div>
  <h2 class="abs video-title">Our Video</h2>
  <p class="abs body-copy video-text">Nemo enim ipsam voluptatem quia voluptas sit aspernatur aut odit aut fugit, sed quia consequuntur magni dolores eos qui ratione voluptatem sequi nesciunt. Neque porro quisquam est, qui dolorem ipsum quia dolor sit amet, consectetur, adipisci velit, sed quia non numquam eius modi tempora incidunt ut labore et dolore magnam aliquam quaerat voluptatem.</p>
  <div class="abs btn video-btn">Watch Video</div>

  <h2 class="abs section-title reviews-title">Customer Reviews</h2>
  <article class="abs review-card" style="left:63px"><div class="quote">“</div><p>Nemo enim ipsam voluptatem quia voluptas sit aspernatur aut odit aut fugit, sed quia consequuntur magni dolores eos qui ratione voluptatem sequi nesciunt. Neque porro quisquam</p><div class="reviewer">Mara Fenwick - USA</div><div class="stars">★★★★★</div></article>
  <article class="abs review-card" style="left:254px"><div class="quote">“</div><p>Nemo enim ipsam voluptatem quia voluptas sit aspernatur aut odit aut fugit, sed quia consequuntur magni dolores eos qui ratione voluptatem sequi nesciunt. Neque porro quisquam</p><div class="reviewer">Pete Calder - UK</div><div class="stars">★★★★★</div></article>
  <article class="abs review-card" style="left:444px"><div class="quote">“</div><p>Nemo enim ipsam voluptatem quia voluptas sit aspernatur aut odit aut fugit, sed quia consequuntur magni dolores eos qui ratione voluptatem sequi nesciunt. Neque porro quisquam</p><div class="reviewer">Anna Holloway - USA</div><div class="stars">★★★★★</div></article>

  <div class="abs team-band"></div>
  <p class="abs team-text">Nemo enim ipsam voluptatem quia voluptas sit aspernatur aut odit aut fugit, sed quia consequuntur magni dolores eos qui ratione voluptatem sequi nesciunt. Neque porro quisquam est, qui dolorem ipsum quia dolor sit amet, consectetur, adipisci velit, sed quia non numquam eius modi tempora incidunt ut labore et dolore magnam aliquam quaerat voluptatem. Ut enim ad minima veniam, quis nostrum exercitationem ullam corporis suscipit laboriosam, nisi ut aliquid ex ea commodi consequatur</p>
  <div class="abs btn team-btn">Meet the Team</div>

  <h2 class="abs section-title news-title">Newsletter Sign-Up</h2>
  <p class="abs news-sub">Sign up with your email address to receive news and updates.</p>
  <div class="abs field" style="left:65px">First Name</div>
  <div class="abs field" style="left:207px">Last Name</div>
  <div class="abs field" style="left:349px">Email Address</div>
  <div class="abs signup">Sign Up</div>

  <footer class="abs site-footer"></footer>
  <div class="abs footer-brand">kestrelbrookhollow.com</div>
  <div class="abs footer-links"><span>Shop</span><span>Terms &amp; Conditions</span><span>Privacy Policy</span><span>FAQs</span><span>Partnership enquiries</span></div>
  <div class="abs socials"><span></span><span></span><span></span><span></span></div>
  <div class="abs copyright">© 2020 All Rights Reserved</div>

  <div class="abs dim"></div>
  <div class="abs gate">
    <div class="gate-offer" role="img" aria-label="Jars of hemp oil and seeds on a wooden table">
      <h2>25% OFF</h2>
      <p>Nemo enim ipsam voluptatem quia voluptas sit aspernatur aut odit aut fugit, sed quia</p>
    </div>
    <div class="gate-panel">
      <h2>Age Verfication</h2>
      <h3>You Must Be 20+ To View This Page</h3>
      <p>Nemo enim ipsam voluptatem quia voluptas sit aspernatur aut odit aut fugit, sed quia consequuntur magni dolores eos qui ratione voluptatem sequi nesciunt</p>
      <div class="gate-actions"><span class="agree">Agree</span><span class="decline">Decline</span></div>
      <div class="abs close">X</div>
    </div>
  </div>
</section>

</div>
</body>
</html>
```